New bussiness card, using company logo.
Lionel Brisk
Manager/Director
Brisk Property Developments
Po Box 5347
Thuringowa Central
Qld
0491 638 205
lionel@briskpropertydevelopments
eye catching, vibrant colours, professional

```html
<!DOCTYPE html>
<html lang="en">
<head>
<meta charset="utf-8">
<title>Brisk Property Developments – Business Cards</title>
<link rel="stylesheet" href="https://fonts.googleapis.com/css2?family=Open+Sans:wght@400;600;700;800&display=swap">
<style>
  :root {
    --backdrop: #2b2623;
    --card-white: #ffffff;
    --brand-red: #e0262b;
    --brand-green: #6dbb45;
    --green-light: #9acb3c;
    --green-deep: #5db447;
    --ink: #222222;
    --ink-soft: #555555;
    --icon-green: #6dbb45;
  }
  * { box-sizing: border-box; margin: 0; padding: 0; }
  html, body { width: 1200px; height: 736px; overflow: hidden; }
  body {
    background: var(--backdrop);
    font-family: "Open Sans", Arial, sans-serif;
    position: relative;
  }
  .card {
    position: absolute;
    width: 556px;
    height: 318px;
    border-radius: 18px;
    overflow: hidden;
  }
  .card--front { left: 32px; top: 36px; background: var(--card-white); }
  .card--red { left: 609px; top: 36px; background: var(--brand-red); }
  .card--white { left: 27px; top: 386px; background: var(--card-white); }
  .card--green {
    left: 612px; top: 386px;
    background: linear-gradient(90deg, var(--green-light), var(--green-deep));
  }

  .brand-name {
    position: absolute;
    left: 0; right: 0;
    text-align: center;
    font-weight: 800;
    line-height: 1.02;
    letter-spacing: 0.5px;
    text-transform: uppercase;
  }
  .brand-name .brand-line { display: block; }
  .card--front .brand-name { top: 66px; font-size: 27px; color: var(--brand-red); }
  .card--red .brand-name { top: 110px; font-size: 38px; color: var(--card-white); }
  .card--white .brand-name { top: 92px; font-size: 38px; color: var(--brand-red); }
  .card--green .brand-name { top: 112px; font-size: 38px; color: var(--card-white); }

  .contact {
    position: absolute;
    left: 0; right: 0;
    text-align: center;
    color: var(--ink);
    font-size: 13.5px;
  }
  .contact--address { top: 181px; }
  .contact--lines {
    top: 204px;
    display: flex;
    justify-content: center;
    gap: 18px;
    align-items: center;
  }
  .contact-item { display: inline-flex; align-items: center; gap: 6px; }
  .contact-icon { width: 11px; height: 11px; }

  .wave { position: absolute; left: 0; bottom: 0; width: 556px; height: 318px; }
  .holder {
    position: absolute;
    left: 17px; top: 284px;
    color: var(--card-white);
    font-size: 15px;
  }
  .holder-name { font-weight: 700; font-size: 16px; }

  .web {
    position: absolute;
    left: 0; right: 0;
    bottom: 24px;
    text-align: center;
    font-size: 15px;
    letter-spacing: 1.4px;
  }
  .card--red .web, .card--green .web { color: var(--card-white); }
  .card--white .web { color: var(--ink); }
</style>
</head>
<body>

  <section class="card card--front" aria-label="Business card front">
    <h1 class="brand-name"><span class="brand-line">Brisk</span><span class="brand-line">Property Developments</span></h1>
    <p class="contact contact--address">Po Box 5347, Thuringowa Central , Qld</p>
    <p class="contact contact--lines">
      <span class="contact-item">
        <svg class="contact-icon" viewBox="0 0 12 12" aria-hidden="true"><circle cx="6" cy="6" r="5.2" fill="none" stroke="var(--icon-green)" stroke-width="1.4"/><path d="M4 3.2 L5.2 3.2 L5.6 5 L4.9 5.5 Q5.6 7 6.6 7.3 L7.1 6.6 L8.8 7 L8.8 8.2 Q5 8.6 4 3.2Z" fill="var(--icon-green)"/></svg>
        0491 638 205
      </span>
      <span class="contact-item">
        <svg class="contact-icon" viewBox="0 0 12 12" aria-hidden="true"><rect x="1" y="3" width="10" height="7" rx="1" fill="var(--icon-green)"/><path d="M1.5 3.5 L6 7 L10.5 3.5" fill="none" stroke="#fff" stroke-width="1"/></svg>
        lionel@briskpropertydevelopments.com
      </span>
    </p>
    <svg class="wave" viewBox="0 0 556 318" aria-hidden="true">
      <defs>
        <linearGradient id="band-green" x1="0" x2="1" y1="0" y2="0">
          <stop offset="0" stop-color="#5db447"/>
          <stop offset="1" stop-color="#9acb3c"/>
        </linearGradient>
      </defs>
      <path d="M0,244 C160,248 300,286 420,294 C482,298 530,276 556,258 L556,318 L0,318Z" fill="var(--brand-red)"/>
      <path d="M0,254 C160,258 300,296 420,303 C484,306 530,286 556,270 L556,318 L0,318Z" fill="#ffffff"/>
      <path d="M0,262 C150,264 300,302 420,310 C485,313 530,294 556,280 L556,318 L0,318Z" fill="url(#band-green)"/>
    </svg>
    <p class="holder"><span class="holder-name">Lionel Brisk,</span> Manager/Director</p>
  </section>

  <section class="card card--red" aria-label="Business card back, red">
    <h2 class="brand-name"><span class="brand-line">Brisk</span><span class="brand-line">Property Developments</span></h2>
    <p class="web">www.briskpropertydevelopments.com</p>
  </section>

  <section class="card card--white" aria-label="Business card back, white">
    <h2 class="brand-name"><span class="brand-line">Brisk</span><span class="brand-line">Property Developments</span></h2>
    <p class="web">www.briskpropertydevelopments.com</p>
  </section>

  <section class="card card--green" aria-label="Business card back, green">
    <h2 class="brand-name"><span class="brand-line">Brisk</span><span class="brand-line">Property Developments</span></h2>
    <p class="web">www.briskpropertydevelopments.com</p>
  </section>

</body>
</html>
```